Web Design Project for Communications Agency

The design I need (PSD file) is for an agency offering specialised PR and communications services for customers in the healthcare sector.

OBJECTIVES OF THE WEBSITE:
1. To promote the agency's communication services
2. To position Solène Brivard as an industry leader, an expert in healthcare PR and communications by highlighting blogposts and social media.

WHAT I NEED:
1st, I need the design for the Home Page ONLY.
Once approved, I will need the other pages designed as well. (Here is prototype that we've already developed for the Website that will guide you in the design:
http://qorvelle.net/solenebrivard/)

VISUAL INSPIRATION
We want to give this Website a "Flat Design" look. Here are some websites for inspiration :
- http://tavrolinkworks.com/#!/process
- http://www.brindlemoss.co/
- http://quellaroft.com/

Also, reuse images found on the company's current Website :
http://www.solenebrivard.com/fr/index.html

HOMEPAGE MAIN ELEMENTS:
1. Main menu : 6 sections
Accueil | Agence | Services | Approche | Publications | Contact

2. Main Call To Action (big dark rectangle in prototype):
Can be slider or just an information bloc.

3. Publications récentes :
The 4 latest blog posts must be features on the homepage (will be linked with the "Publications" section)

4. Dynamic Footer :
Contains a Chirpline feed and a Subscribe to our Newsletter feature (revecez nos publications)

OTHER PAGES (to design once Homepage is approved)
- Agence (about us)
- Services (our team)
- Approche (our approach)
- Publications (blog articles)
- Contact (Contact us)

Industry/Entity Type

Communications

Requirements
Must have
• Please refer to prototype :
http://qorvelle.net/solenebrivard/
Must have ALL features present in prototype.

Also, must reuse this picture in the design : http://solenebrivard.com/static/images/home-big-box.jpg

Finally, you will find attached the company logo.

```html
<!DOCTYPE html>
<html lang="fr">
<head>
<meta charset="utf-8">
<title>Solène Brivard — Services</title>
<link href="https://fonts.googleapis.com/css2?family=Lato:wght@300;400;700;900&display=swap" rel="stylesheet">
<style>
:root{
  --red:#e9533b;
  --ink:#333333;
  --text:#7a7a7a;
  --band:#e6e6e6;
  --icon-bg:#e4e4e4;
  --footer:#4b4b4b;
  --field:#3a3a3a;
  --white:#ffffff;
}
*{margin:0;padding:0;box-sizing:border-box}
html,body{width:1200px;height:2236px;overflow:hidden;background:var(--white)}
body{font-family:"Lato",sans-serif;color:var(--text);position:relative}

.site-header{position:absolute;left:0;top:0;width:1200px;height:155px;background:var(--red)}
.brand{position:absolute;left:150px;top:14px;color:var(--white);font-weight:700;font-size:50px;line-height:50px;letter-spacing:-1px;text-transform:lowercase}

.main-nav{position:absolute;left:0;top:155px;width:1200px;height:63px;background:var(--white);border-bottom:1px solid #dddddd}
.tagline{position:absolute;left:150px;top:17px;font-size:12px;line-height:15px;color:var(--ink);font-weight:400;letter-spacing:.5px;text-transform:uppercase}
.nav-list{list-style:none;position:absolute;top:24px;left:0}
.nav-list li{position:absolute;font-size:13px;letter-spacing:.5px;color:#8a8a8a;text-transform:uppercase;white-space:nowrap}
.nav-list li.is-active{color:var(--red)}

.page-intro{position:absolute;left:0;top:218px;width:1200px;height:242px;background:var(--band)}
.page-title{position:absolute;left:150px;top:40px;color:var(--red);font-weight:300;font-size:40px;line-height:50px}
.page-lead{position:absolute;left:150px;top:104px;width:895px;font-size:14px;line-height:22px;color:#707070}
.notch-down{position:absolute;left:583px;top:460px}

.section-label{position:absolute;left:150px;top:494px;color:var(--red);font-size:18px;font-weight:400;letter-spacing:.3px;text-transform:uppercase}

.service{position:absolute;width:435px}
.service-head{display:flex;align-items:center;height:66px}
.service-icon{width:66px;height:66px;border-radius:50%;background:var(--icon-bg);flex:none;display:flex;align-items:center;justify-content:center}
.service-title{margin-left:27px;color:var(--ink);font-weight:700;font-size:20px;line-height:26px}
.service-body{margin-top:28px;font-size:11.5px;line-height:19.5px;text-align:justify}
.service-body p+p{margin-top:18px}

.site-footer{position:absolute;left:0;top:1781px;width:1200px;height:455px;background:var(--footer)}
.notch-footer{position:absolute;left:583px;top:0}
.feed-label{position:absolute;left:150px;top:35px;color:var(--white);font-weight:900;font-size:22px;letter-spacing:-.5px}
.tweet{position:absolute;left:150px;width:250px;display:flex}
.tweet-avatar{width:55px;height:50px;background:linear-gradient(160deg,#c79a7e,#8e6a55);flex:none}
.tweet-text{margin-left:26px;font-size:9.5px;line-height:12.5px;color:#e0e0e0;text-align:justify}
.tweet-text a{display:block;color:var(--red);text-decoration:none}
.follow-btn{position:absolute;left:150px;top:338px;width:185px;height:30px;background:var(--red);color:var(--white);font-size:10.5px;font-weight:700;line-height:30px;padding-left:20px}

.newsletter-title{position:absolute;left:467px;top:36px;color:var(--white);font-size:19px;letter-spacing:.5px;text-transform:uppercase;font-weight:400}
.field{position:absolute;left:467px;width:584px;height:45px;background:var(--field);color:#8d8d8d;font-size:12px;line-height:45px;padding-left:12px}
.subscribe-btn{position:absolute;left:467px;top:231px;width:129px;height:38px;background:var(--red);color:var(--white);font-size:11px;line-height:38px;text-align:center}
.copyright{position:absolute;left:932px;top:350px;font-size:8.5px;line-height:12px;color:#8a8a8a}
</style>
</head>
<body>

<header class="site-header">
  <div class="brand">solène<br>brivard</div>
</header>

<nav class="main-nav">
  <div class="tagline">Gestion d'enjeux<br>Affaires publiques</div>
  <ul class="nav-list">
    <li class="is-active" style="left:362px">Agence</li>
    <li style="left:503px">Services</li>
    <li style="left:641px">Approche</li>
    <li style="left:773px">Publications</li>
    <li style="left:934px">Contact</li>
  </ul>
</nav>

<section class="page-intro">
  <h1 class="page-title">Services</h1>
  <p class="page-lead">Lorem ipsum dolor sit amet, consectetur adipisicing elit, sed do eiusmod tempor incididunt ut labore et dolore magna aliqua. Ut enim ad minim veniam. Lorem ipsum dolor sit amet.Consectetur adipisicing elit, sed do eiusmod tempor incididunt. Ut labore et dolore magna aliqua. Ut enim ad minim veniam.</p>
</section>
<svg class="notch-down" width="34" height="17" viewBox="0 0 34 17"><path d="M0 0h34L17 17z" fill="#e6e6e6"/></svg>

<h2 class="section-label">Liste des services</h2>

<article class="service" style="left:150px;top:563px">
  <div class="service-head">
    <div class="service-icon"><svg width="34" height="34" viewBox="0 0 34 34"><rect x="3" y="6" width="28" height="25" rx="2" fill="#e9533b"/><rect x="9" y="2" width="3" height="8" fill="#e9533b"/><rect x="22" y="2" width="3" height="8" fill="#e9533b"/><g fill="#fff"><rect x="7" y="14" width="5" height="4"/><rect x="14.5" y="14" width="5" height="4"/><rect x="22" y="14" width="5" height="4"/><rect x="7" y="21" width="5" height="4"/><rect x="14.5" y="21" width="5" height="4"/><rect x="22" y="21" width="5" height="4"/></g></svg></div>
    <h3 class="service-title">Planification stratégique</h3>
  </div>
  <div class="service-body">
    <p>Parfois, il est difficile de voir clair. Vous connaissez vos produits et services, mais les priorités sont trop nombreuses. Tout s'entremêle et la mission perd de sa netteté au fil des opérations. Les détails prennent le pas sur le fond. Vous perdez en perspective. Et évidemment, chaque membre de votre équipe a ses incontournables, ses impondérables. Comment établir une vision claire et commune des prochaines étapes ?</p>
    <p>C'est là que nous intervenons. En organisant et en animant vos journées de planification stratégique, nous intégrons les orientations convenues dans un plan qui regroupe les idées et les contraintes exprimées dans le respect des participants.</p>
  </div>
</article>

<article class="service" style="left:631px;top:563px">
  <div class="service-head">
    <div class="service-icon"><svg width="36" height="32" viewBox="0 0 36 32"><path d="M4 2h18a3 3 0 013 3v11a3 3 0 01-3 3H12l-6 5v-5H4a3 3 0 01-3-3V5a3 3 0 013-3z" fill="#e9533b"/><path d="M28 10h4a3 3 0 013 3v9a3 3 0 01-3 3h-1v5l-6-5h-8a3 3 0 01-3-3v-1h8a6 6 0 006-6z" fill="#e9533b"/></svg></div>
    <h3 class="service-title">Plan de communication</h3>
  </div>
  <div class="service-body">
    <p>La communication ne se fait pas seule. Elle est un levier pour vous permettre d'atteindre vos objectifs d'affaires. Nous élaborons des stratégies innovatrices pour vous positionner efficacement.</p>
    <p>Nos stratégies allient plusieurs disciplines : relations gouvernementales, communications, marketing, organisation d'événements, relations de presse, etc. Nous mettons de l'ordre dans vos priorités pour marquer le rayonnement de votre organisation de manière structurée. Nous transformons vos orientations en réalisations.</p>
  </div>
</article>

<article class="service" style="left:150px;top:918px">
  <div class="service-head">
    <div class="service-icon"><svg width="34" height="34" viewBox="0 0 34 34"><path d="M16 2c8 0 14 6 14 13 0 3-1 5-3 7v10H13v-5H8a2 2 0 01-2-2v-5H3l3-6C6 7 10 2 16 2z" fill="#e9533b"/><circle cx="17" cy="13" r="4" fill="#fff"/></svg></div>
    <h3 class="service-title">Conseil stratégique</h3>
  </div>
  <div class="service-body">
    <p>Dans la vie d'une organisation, surviennent des événements inattendus qui commandent une action immédiate. Des événements qui suscitent une vive attention du public, une opportunité à saisir. Sur des enjeux ponctuels, nous développons des stratégies et des argumentaires. Que ce soit dans le cadre de commissions parlementaires, de crises médiatiques, d'enjeux entre partenaires d'une même industrie ou de revendications auprès d'une autorité réglementaire.</p>
  </div>
</article>

<article class="service" style="left:631px;top:918px">
  <div class="service-head">
    <div class="service-icon"><svg width="34" height="34" viewBox="0 0 34 34"><circle cx="17" cy="17" r="15" fill="#e9533b"/><circle cx="17" cy="17" r="11" fill="#fff"/><path d="M16 9h2.5v8.5l5 3-1.3 2-6.2-3.8z" fill="#e9533b"/></svg></div>
    <h3 class="service-title">Gestion efficace d'assemblées générales</h3>
  </div>
  <div class="service-body">
    <p>Pour une association, un syndicat professionnel ou une entreprise, l'organisation d'une assemblée générale ou des propositions cruciales seront débattues est souvent une source d'inquiétude. Pour d'autres, c'est une occasion pour mobiliser la base. Une assemblée générale, ça se prépare. Nous organisons les assemblées en préparant l'avant, le pendant et l'après assemblée. Nous rédigeons les discours et anticipons tous les scénarios possibles.</p>
  </div>
</article>

<article class="service" style="left:150px;top:1197px">
  <div class="service-head">
    <div class="service-icon"><svg width="26" height="36" viewBox="0 0 26 36"><rect x="8" y="1" width="10" height="20" rx="5" fill="#e9533b"/><path d="M3 15a10 10 0 0020 0" stroke="#e9533b" stroke-width="3" fill="none"/><rect x="11.5" y="25" width="3" height="7" fill="#e9533b"/><rect x="6" y="32" width="14" height="3" fill="#e9533b"/></svg></div>
    <h3 class="service-title">Coaching de porte-parole</h3>
  </div>
  <div class="service-body">
    <p>Réussir une entrevue, ce n'est pas donné à tous. Trop nombreux sont ceux qui oublient l'auditoire. Trop concentrés sur les messages organisationnels ou embourbés dans un langage que le public comprend mal. Ils trébuchent. On ne prépare pas une entrevue en direct à la télé ou à la radio de la même manière qu'un entretien avec un journaliste de la presse écrite. Nous aidons nos clients à faire passer leur message clairement autant dans les médias que lors de tribunes publiques. Clarté, intégrité et efficacité guident notre approche.</p>
  </div>
</article>

<article class="service" style="left:631px;top:1197px">
  <div class="service-head">
    <div class="service-icon"><svg width="38" height="26" viewBox="0 0 38 26"><path d="M1 5l8-3 5 3h6l6-3 11 4-4 12-5 4-4-3-4 3-4-3-4 2L2 14z" fill="#e9533b"/><path d="M13 9l6-2 6 6-3 2z" fill="#fff"/></svg></div>
    <h3 class="service-title">Relations gouvernementales</h3>
  </div>
  <div class="service-body">
    <p>C'est en tablant sur des relations interpersonnelles de qualité avec les décideurs que vous établirez la crédibilité de ceux que vous représentez, mais aussi votre notoriété personnelle comme dirigeant. Notre approche : identifier les bons interlocuteurs, vous aider à positionner votre dossier en tenant compte des enjeux politiques qui guident les décisions des autorités gouvernementales. C'est là que nous excellons !</p>
  </div>
</article>

<article class="service" style="left:150px;top:1475px">
  <div class="service-head">
    <div class="service-icon"><svg width="34" height="32" viewBox="0 0 34 32"><circle cx="17" cy="8" r="5" fill="#e9533b"/><circle cx="7" cy="12" r="4" fill="#e9533b"/><circle cx="27" cy="12" r="4" fill="#e9533b"/><path d="M9 30v-9a8 8 0 0116 0v9z" fill="#e9533b"/><path d="M1 28v-6a6 6 0 0110-4v10z M33 28v-6a6 6 0 00-10-4v10z" fill="#e9533b"/></svg></div>
    <h3 class="service-title">Conférence et tables rondes</h3>
  </div>
  <div class="service-body">
    <p>Nous présentons des conférences dans le cadre de congrès, de colloques de formation, de sessions de planification stratégique destinées à des professionnels de la santé et des gestionnaires. Communications avec les patients, mise en marché de services professionnels, éthique dans les pratiques commerciales et professionnelles, gouvernance, gestion du risque à la réputation, portrait des tendances ailleurs au Canada et aux États-Unis, voilà autant de sujets que nous abordons.</p>
  </div>
</article>

<footer class="site-footer">
  <svg class="notch-footer" width="34" height="17" viewBox="0 0 34 17"><path d="M0 0h34L17 17z" fill="#ffffff"/></svg>

  <div class="feed-label">Chirpline</div>

  <div class="tweet" style="top:99px">
    <div class="tweet-avatar" role="img" aria-label="Photo de profil de l'auteur du message"></div>
    <p class="tweet-text">Velit esse cillum dolore eu fugiat nulla pariatur. Excepteur sint occaecat cupidatat non proident.<a>#SoleneBrivard @SoleneBrivard</a></p>
  </div>
  <div class="tweet" style="top:172px">
    <div class="tweet-avatar" role="img" aria-label="Photo de profil de l'auteur du message"></div>
    <p class="tweet-text">Velit esse cillum dolore eu fugiat nulla pariatur. Excepteur sint occaecat cupidatat non proident.<a>#SoleneBrivard @SoleneBrivard</a></p>
  </div>
  <div class="tweet" style="top:246px">
    <div class="tweet-avatar" role="img" aria-label="Photo de profil de l'auteur du message"></div>
    <p class="tweet-text">Velit esse cillum dolore eu fugiat nulla pariatur. Excepteur sint occaecat cupidatat non proident.<a>#SoleneBrivard @SoleneBrivard</a></p>
  </div>

  <div class="follow-btn">Suivre @SoleneBrivard</div>

  <h2 class="newsletter-title">Recevez nos publications</h2>
  <div class="field" style="top:102px">Votre nom</div>
  <div class="field" style="top:162px">Votre courriel</div>
  <div class="subscribe-btn">Abonnez-vous</div>

  <p class="copyright">© 2013 Solène Brivard<br>Tous droits réservés</p>
</footer>

</body>
</html>
```